Nutritional & Gastrointestinal Health Consulting Service-Website design

We need a website design for a new health consulting service called "Bright Vale" based in Perth, Australia.

We will be providing consulting services in the areas of:
1) Nutrition and Diet
2) Gastrointestinal Health (which means stomach & digestive system related health)

These consulting services will be provided by an Accredited Dietitian and a Paediatric Gastroenterologist.

We are open to creative ideas in terms of design, layout, fonts and colours. We also would love to see images of nature in the backdrop with families (adults with kids) having a good time, fresh fruits and vegetables displayed in a farmer's market or supermarket. 2 or 3 images should be sufficient. We would also definitely want our logo somewhere in the main page of website. The logo file is also attached. Please have a look at a website's design that we really liked. We would love to see designs inspired by that style. The website details are in the in the "nice to have priorities" section of this project brief.

We also would be looking at website designers with software coding skills so that if we like the design we can go ahead with the next step of coding.

The website design should communicate the purpose of the website and at the same time be simple, elegant and unique/eye-catching.

We look forward to receiving creative ideas for our website from you all. Good luck!

More details have been added to our project- for example: Logo, fonts style, must haves etc etc. Please view the updated project brief. Looking forward to receiving your fantastic ideas for our website. Thanking you

Hi, I have updated the colour preference. Will add the content preferences tomorrow. thanks

Hello all, I have now added a LOT more content to what we want in our website. It is very much in detail, so please carefully have a read through the entire project brief. If you have any questions write back to me and I will try to respond as quickly as I can. Last few days were busy so couldn't respond quickly to all of you who had send me designs/queries/questions. Thank you for your patience. I look forward to receiving fantastic designs from you all. Good Luck :-)

Target Market(s)

Adults based in western speaking countries aged 18 to 60 years

Industry/Entity Type

Software

Font styles to use
Sans Serif
Script

Colors
faa54b
acd036

Requirements
Must have
• The website must have the MAIN logo file attached. I have attached 3 files: 1) MAIN logo; 2) supplementary logo A ; 3) supplementary logo B

I have selected 2 colours from the colour scheme (see below)-(as the colour of our logo is that).
However we would also like to see LIGHT CHOCOLATE BROWN or CHOCOLATE BROWN colour used as the background colour of the website
Preferred WEBSITE CONTENT:
1) HOME PAGE:
Content required=
--Company Logo
--Dr Dorian Pelham
Paediatric Gastroenterologist & Hepatologist
-Marla Pelham.
Dietitian & Nutritionist
--Website Menu (either listed horizontally or vertically):
Once clicked on each name:

Under each of the Website Menu items we want the following Headings to be added

2) ABOUT US page:
Sub-heading under this: Qualification, Skills, Special Interest

3) SERVICES
DORIAN'S PAGE: Individual Consultation, Endoscopy procedures
Individual Consultation, Group Based Services, Food Diary, Food & Symptom Diary

4) FEES & REBATE: Content as below:
Please Note: Payment of full fees is required at the time of consultation and procedures. 48 hours notice is required for cancellation of appointments/non-attendance. Failure to provide this may result in a fee being incurred. Please call reception to find out the amount of fee charged for cancellation of appointments/non-attendance.
headings are:
Paediatric Gastroenterology:
Dorian's pge
Individual Consultation - Initial (upto 30 mins):
Review Consultation (upto 15 mins):
Endoscopy procedures - No Gap fees charged. Fees will be billed directly to Vitacover. If any queries, please contact reception.

marla's pge
sub heading:
Individual Consultation - Initial (upto 45 mins):
Individual Consultation - Review (upto 30 mins):

Concession-Individual Consultation -Initial (upto 45 mins):
Concession-Individual Consultation - Review (upto 30 mins):
Please Note: Concession applies for health care card holders & pensioners

Group Based Services: Pricing subject to the type of service provided. Please contact us for an obligation free quote.
Education Topics Include:
- Paediatric Nutrition (Introducing Solids, Fussy Eating, Healthy Eating)
- Pregnancy Nutrition, Gestational Diabetes, Breastfeeding/Lactation Nutrition
- Healthy Eating, Supermarket Shopping Tips, Nutrition Label Reading Tips, Healthier
sub heading under nutrition & diet:
-Vitacover:
--A rebate of $52.95 is available from Vitacover if an EPC ( Enhanced Primary Care)/Chronic Disease Management (CDM) plan is issued by your GP.
--All mandatory paperwork needs to be available at the time of making your appointment for your eligibility.
-Private Health Fund:
--Most private health funds provide rebate on dietetic appointments. However the rebate amount depends on your level of cover. Thus, please contact your health fund to determine your entitled rebate.
-RSB: Approved provider for RSB services

6) FOR DOCTORS: Bright Vale Paediatric Gastroenterologist Referral Form
Bright Vale Dietitian Referral form
7) LOCATIONS & CONTACT

Paediatric Gastroenterology & Hepatology Service
Suite 46
Holy Lantern Bramcote Medical Centre
17 Colin Ferris Pde,
MURDOCH, WA 6150
P: (08) 9422 5061
F: (08) 9422 3094

Nutrition & Diet Service
Suite 46
17 Colin Ferris Pde,
MURDOCH, WA 6150
P: (08) 9422 5061
F: (08) 9422 3094

Tolland Medical Centre
58-60 Karrigan Parkway,
MANDURAH, WA 6210
P: (08) 9647 2283
F: (08) 96724419
www.tmcexample.com.au

This page should have a webform that has following titles:
-Your Name
-Your Email
-Your Phone
-Message

8) NEWS & BLOG
Nice to have
• We liked the design style of the websites below:
https://www.vendoraplex.example/

http://qoravelt.example/

But feel free to use your creativity too
Should not have
• Please do not use any body building or muscle building images

```html
<!DOCTYPE html>
<html lang="en">
<head>
<meta charset="utf-8">
<title>Bright Vale – For Doctors</title>
<link rel="stylesheet" href="https://fonts.googleapis.com/css2?family=Arimo:wght@400;700&display=swap">
<style>
  :root {
    --bg-dark: #5a3418;
    --bg-mid: #7a4a28;
    --shell: rgba(214, 196, 182, 0.82);
    --panel-brown: #7d5d48;
    --panel-light: rgba(232, 224, 220, 0.9);
    --frame: #ffffff;
    --heading-brown: #5b3420;
    --link-orange: #f5a53c;
    --link-lime: #e2f25a;
    --ink: #111111;
    --brand-green: #a9cd3a;
  }
  * { box-sizing: border-box; margin: 0; padding: 0; }
  html, body { width: 1200px; height: 615px; overflow: hidden; }
  body {
    position: relative;
    font-family: "Arimo", Arial, sans-serif;
    color: var(--ink);
  }
  .backdrop {
    position: absolute; inset: 0;
    background: radial-gradient(circle at 50% 40%, var(--bg-mid), var(--bg-dark));
  }
  .shell {
    position: absolute; left: 35px; top: 37px; width: 1131px; height: 540px;
    background: var(--shell);
    border: 2px solid var(--frame);
    border-radius: 14px;
  }
  .account-links {
    position: absolute; right: 43px; top: 7px;
    font-size: 13px; color: #6b4a30;
  }
  .account-links a { color: #6b4a30; }
  .account-links .divider { margin: 0 8px; color: #fff; }
  .masthead {
    position: absolute; left: 215px; top: 24px; width: 698px; height: 177px;
    background: var(--panel-brown);
    border: 3px solid var(--frame);
    border-radius: 16px;
    display: flex; align-items: flex-end; justify-content: center;
    padding-bottom: 26px;
  }
  .brand-name {
    font-size: 34px; font-weight: 700; letter-spacing: 1px;
    color: var(--brand-green);
  }
  .box {
    position: absolute;
    border: 3px solid var(--frame);
    border-radius: 6px;
  }
  .box-title {
    color: #fff; font-weight: 700; font-size: 15px;
    text-align: center; padding: 5px 0 6px;
    border-bottom: 3px solid #e7e1dc;
  }
  .main-menu {
    left: 25px; top: 219px; width: 224px; height: 242px;
    background: var(--panel-brown);
  }
  .main-menu ul { margin: 20px 0 0 58px; font-size: 13px; font-weight: 700; line-height: 17.6px; }
  .main-menu li::marker { color: #d8c7b8; }
  .main-menu a { color: var(--link-orange); }
  .main-menu a.alt { color: var(--link-lime); }
  .content {
    left: 259px; top: 219px; width: 609px; height: 233px;
    background: var(--panel-light);
    padding: 5px 12px 0 12px;
  }
  .breadcrumb {
    font-size: 13px; font-weight: 700;
    padding: 0 0 2px 10px;
    border-bottom: 3px solid #c9c1bc;
  }
  .breadcrumb a { color: var(--ink); }
  .page-title { font-size: 20px; font-weight: 700; color: var(--heading-brown); margin: 12px 0 0 0; }
  .forms-block { margin: 30px 12px 0 12px; border-bottom: 3px solid #c9c1bc; padding-bottom: 22px; }
  .forms-block h2 { font-size: 16px; font-weight: 700; margin-bottom: 17px; }
  .forms-block p { font-size: 14px; font-weight: 700; margin-bottom: 15px; }
  .forms-block p:last-child { margin-bottom: 0; }
  .forms-block a { color: var(--ink); }
  .user-login {
    left: 878px; top: 219px; width: 225px; height: 214px;
    background: var(--panel-brown);
    color: #fff;
  }
  .login-form { padding: 14px 0 0 16px; font-size: 13px; }
  .login-form label { display: block; font-weight: 700; }
  .login-form .req { color: #e43; }
  .login-form input[type=text], .login-form input[type=password] {
    width: 108px; height: 20px; border: 1px solid #999; margin: 1px 0 14px;
    font: 13px "Arimo", Arial, sans-serif; padding: 0 2px;
  }
  .login-form ul { margin: -4px 0 14px 7px; padding-left: 14px; }
  .login-form ul a { color: var(--link-lime); }
  .login-form button {
    font: 13px "Arimo", Arial, sans-serif; padding: 1px 6px;
    background: #eee; border: 1px solid #888; border-radius: 2px;
  }
  .footer {
    position: absolute; left: 0; right: 0; top: 501px;
    text-align: center; font-size: 12px; font-weight: 700;
  }
  .footer a { color: var(--ink); }
</style>
</head>
<body>
  <div class="backdrop" role="img" aria-label="Chocolate brown background with a faint pattern of sketched fruit and vegetables"></div>
  <div class="shell">
    <nav class="account-links"><a href="#">Login</a><span class="divider">|</span><a href="#">Register</a></nav>

    <header class="masthead">
      <span class="brand-name">BRIGHT VALE</span>
    </header>

    <aside class="box main-menu">
      <div class="box-title">Main menu</div>
      <ul>
        <li><a href="#">Home</a></li>
        <li><a href="#">About Us</a></li>
        <li><a href="#">Nutrition &amp; Diet</a></li>
        <li><a href="#">Paediatric Gastroenterology</a></li>
        <li><a href="#">Fees &amp; Rebate</a></li>
        <li><a href="#">For Doctors</a></li>
        <li><a class="alt" href="#">Location</a></li>
        <li><a class="alt" href="#">Contact</a></li>
        <li><a class="alt" href="#">News &amp; Blog</a></li>
      </ul>
    </aside>

    <main class="box content">
      <div class="breadcrumb"><a href="#">Home</a></div>
      <h1 class="page-title">For Doctors</h1>
      <section class="forms-block">
        <h2>Downloadable Referral Forms</h2>
        <p><a href="#">Bright Vale Paediatric Gastroenterologist Referral Form</a></p>
        <p><a href="#">Bright Vale Dietitian Referral Form</a></p>
      </section>
    </main>

    <aside class="box user-login">
      <div class="box-title">User login</div>
      <form class="login-form">
        <label>Username <span class="req">*</span></label>
        <input type="text" value="Tamsin">
        <label>Password <span class="req">*</span></label>
        <input type="password" value="passwordxyz">
        <ul><li><a href="#">Request new password</a></li></ul>
        <button type="button">Log in</button>
      </form>
    </aside>

    <footer class="footer"><a href="#">Bright Vale</a> © Copyright 2014</footer>
  </div>
</body>
</html>
```